Web Developer Needs a Business Card Design

I need a personal business card design that represents me as a web developer for potential employers. I would like the background to be a dark color on the front for contrast with my logo and name. The back will have all my information along with a smaller version of the logo. I want something with a modern look and feel, not too conservative. This will be used for potential employers and freelance work.

Industry/Entity Type

Business

Contact Information for Business Card

Front should have my logo and name. The back should have all my personal information which would include: name: Tom Varulek, phone: 570-614-3098, email: tomvarulek@quillbox.net, website url: www.tomvarulek.net, logo, web developer.

Font styles to use
Sans Serif

Requirements
Must have
• Must include my logo. The color palette base color will be the logo color.

```html
<!DOCTYPE html>
<html lang="en">
<head>
<meta charset="utf-8">
<title>Tom Varulek — Business Card</title>
<link href="https://fonts.googleapis.com/css2?family=Lato:wght@400;700&display=swap" rel="stylesheet">
<style>
  :root {
    --brand: #248c72;
    --ink: #1c1c1c;
    --paper: #ffffff;
    --backdrop: #1b1b1b;
  }
  * { margin: 0; padding: 0; box-sizing: border-box; }
  html, body {
    width: 1200px; height: 1086px; overflow: hidden;
    background: var(--backdrop);
    font-family: "Lato", sans-serif;
  }
  .canvas { position: relative; width: 1200px; height: 1086px; }
  .card {
    position: absolute; left: 254px; width: 677px; height: 387px;
    border-radius: 10px; overflow: hidden;
  }
  .card--front { top: 126px; background: var(--paper); }
  .card--back { top: 586px; background: var(--brand); }

  .brand-mark { position: absolute; left: 500px; top: 38px; width: 96px; height: 96px;
    border: 7px solid var(--brand); border-radius: 50%; }
  .brand-name { position: absolute; left: 408px; width: 280px; top: 143px; text-align: center;
    color: var(--brand); font-weight: 700; font-size: 24px; letter-spacing: 0.2px; }

  .holder-name { position: absolute; left: 41px; top: 192px; color: var(--brand);
    font-weight: 700; font-size: 27px; line-height: 1.2; }
  .holder-role { position: absolute; left: 41px; top: 227px; color: var(--ink);
    font-size: 21px; line-height: 1.2; white-space: nowrap; }
  .divider { position: absolute; left: 186px; right: 0; top: 241px; height: 2px; background: var(--ink); }

  .contact-list { position: absolute; left: 38px; top: 267px; list-style: none; }
  .contact-list li { display: flex; align-items: center; height: 26.5px;
    font-size: 21.5px; color: var(--ink); white-space: nowrap; }
  .contact-list svg { width: 22px; height: 20px; margin-right: 7px; fill: var(--brand); flex: none; }

  .back-mark { position: absolute; left: 249px; top: 103px; width: 184px; height: 184px;
    border: 14px solid var(--paper); border-radius: 50%;
    display: flex; align-items: center; justify-content: center; }
  .back-mark span { color: var(--paper); font-weight: 700; font-size: 16px;
    letter-spacing: 0.3px; white-space: nowrap; }
  .back-url { position: absolute; left: 0; right: 0; top: 340px; text-align: center;
    color: var(--paper); font-size: 21px; letter-spacing: 0.6px; }
</style>
</head>
<body>
<main class="canvas">
  <section class="card card--front">
    <div class="brand-mark"></div>
    <div class="brand-name">TOM VARULEK</div>

    <h1 class="holder-name">Tom Varulek</h1>
    <p class="holder-role">Web Developer</p>
    <div class="divider"></div>

    <ul class="contact-list">
      <li>
        <svg viewBox="0 0 22 20"><path d="M2 7c0-3 4-4 9-4s9 1 9 4v2h-4V7H6v2H2z"/><path d="M5 10h12l2 7H3z"/></svg>
        570-614-3098
      </li>
      <li>
        <svg viewBox="0 0 22 20"><path d="M1 3h20v14H1z"/><path d="M2 4l9 7 9-7" stroke="#fff" stroke-width="1.6" fill="none"/><path d="M2 16l7-6M20 16l-7-6" stroke="#fff" stroke-width="1.4"/></svg>
        tomvarulek@quillbox.net
      </li>
      <li>
        <svg viewBox="0 0 22 22" style="fill:none;stroke:var(--brand);stroke-width:1.8"><circle cx="11" cy="11" r="9.5"/><ellipse cx="11" cy="11" rx="4" ry="9.5"/><path d="M1.5 11h19M3 6h16M3 16h16"/></svg>
        www.tomvarulek.net
      </li>
    </ul>
  </section>

  <section class="card card--back">
    <div class="back-mark"><span>TOM VARULEK</span></div>
    <p class="back-url">www.tomvarulek.net</p>
  </section>
</main>
</body>
</html>
```